New Mechanical Maintenance business needs website

New Mechanical Maintenance business in Perth Western Australia needs a nice and easy to navigate website. Showing what we do and how we can be the right fit for other small to medium size business by offering personalized service from our highly skilled team. We deal with both fixed plant repairs like food and chemical processing facilities to heavy equipment like drill rigs, Large boats and earthmoving equipment.

Target Market(s)

Small to medium business to offer personalized services/packages

Industry/Entity Type

e deal with both fixed plant repairs like food and chemical processing facilities to heavy equipment like drill rigs, Large boats and earthmoving equipment.

Coding

Coded - Design and coding required

Number of Pages Required

4 page

Font styles to use
Serif

Colors
0054AA
0677BA
7BADD7
CADEEF
E8F1F8

Requirements
Must have
• A website that is easy to navigate but covers off on the range of services/maintenance we can provide

```html
<!DOCTYPE html>
<html lang="en">
<head>
<meta charset="utf-8">
<title>Keelbrook Maintenance</title>
<link rel="stylesheet" href="https://fonts.googleapis.com/css2?family=Raleway:wght@400;600;700;800&family=Roboto:wght@300;400;500&family=Playfair+Display:wght@700&display=swap">
<style>
:root{
  --blue:#0054AA;
  --blue-mid:#0677BA;
  --blue-soft:#7BADD7;
  --blue-pale:#CADEEF;
  --blue-mist:#E8F1F8;
  --slate:#5a6070;
  --ink:#222;
  --white:#fff;
}
*{margin:0;padding:0;box-sizing:border-box}
html,body{width:1200px;height:4009px;overflow:hidden}
body{position:relative;font-family:"Roboto",Arial,sans-serif;color:var(--ink);background:var(--white)}
.abs{position:absolute}
section,header,footer{position:absolute;left:0;width:1200px}

/* header */
.site-header{top:0;height:193px;background:var(--white)}
.topbar{top:0;left:0;width:1200px;height:47px;background:linear-gradient(90deg,#6b7185,var(--slate));clip-path:polygon(270px 0,1200px 0,1200px 47px,316px 47px)}
.topbar-text{left:328px;top:14px;color:var(--white);font-size:14px}
.social{top:12px;width:24px;height:24px;border-radius:50%;background:var(--white)}
.brand-panel{left:0;top:0;width:320px;height:162px;border-bottom:4px solid var(--blue)}
.brand{left:110px;top:50px;display:flex;align-items:center;gap:12px}
.brand-square{width:40px;height:40px;background:var(--slate);flex:none}
.brand-name{font-family:"Raleway",sans-serif;font-weight:700;font-size:20px;color:var(--slate);line-height:1.2}
.contact-item{top:66px;display:flex;align-items:center;gap:12px;font-size:15px;color:var(--ink);line-height:1.35}
.contact-icon{width:52px;height:52px;border-radius:50%;background:var(--slate);display:flex;align-items:center;justify-content:center;flex:none}
.navbar{top:137px;left:0;width:1200px;height:56px;background:var(--blue);clip-path:polygon(310px 0,1200px 0,1200px 56px,265px 56px)}
.nav-link{top:156px;color:var(--white);font-size:15px}

/* hero */
.hero{top:193px;height:616px;background:linear-gradient(100deg,#0b0d12 0%,#20252c 35%,#3a4a5a 55%,#1f4f96 78%,#2a5ea8 100%)}
.hero-welcome{left:110px;top:136px;color:var(--white);font-size:30px;font-weight:300}
.hero-title{left:110px;top:176px;color:var(--white);font-family:"Playfair Display",Georgia,serif;font-size:62px;line-height:1}
.hero-title small{font-family:"Roboto",sans-serif;font-size:24px;font-weight:300}
.hero-text{left:110px;top:258px;width:330px;color:var(--white);font-size:15px;line-height:28px}
.btn{display:flex;align-items:center;justify-content:center;border-radius:18px;font-size:15px;height:36px}
.hero-btn{left:110px;top:320px;width:114px;background:var(--white);color:var(--ink)}

/* section headings */
.eyebrow{font-family:"Raleway",sans-serif;font-weight:700;font-size:19px;display:flex;align-items:center;gap:6px}
.eyebrow .rule{width:68px;height:4px;background:currentColor}
.sec-title{font-family:"Raleway",sans-serif;font-weight:800;font-size:42px;letter-spacing:.5px}
.centered{left:0;width:1200px;justify-content:center;text-align:center}
.body-copy{font-size:14.5px;line-height:28px}

/* about */
.about{top:809px;height:610px}
.about-name{left:115px;top:110px;width:475px;height:380px;display:flex;align-items:center;justify-content:center;text-align:center;font-family:"Raleway",sans-serif;font-weight:700;font-size:46px;line-height:1.2;color:var(--slate)}
.about .eyebrow{left:645px;top:96px;color:var(--ink)}
.about .eyebrow .rule{background:var(--blue)}
.about .sec-title{left:645px;top:120px;color:var(--blue)}
.about .body-copy{left:645px;top:201px;width:450px}
.blue-btn{background:var(--blue);color:var(--white);width:112px}

/* services */
.services{top:1419px;height:574px;background:var(--blue);color:var(--white)}
.services .eyebrow{top:44px}
.services .sec-title{top:72px}
.svc-card{top:163px;width:280px}
.svc-img{width:280px;height:228px;border-radius:8px}
.svc-name{font-family:"Raleway",sans-serif;font-weight:700;font-size:20px;margin-top:18px}
.svc-text{font-size:14.5px;line-height:28px;margin-top:6px}
.svc-more{font-size:14.5px;text-decoration:underline;margin-top:6px;display:block;color:var(--white)}
.arrow{width:28px;height:28px;border-radius:50%;display:flex;align-items:center;justify-content:center}

/* origin */
.origin{top:1993px;height:512px}
.origin .eyebrow{left:110px;top:112px;color:var(--ink)}
.origin .eyebrow .rule{background:var(--blue)}
.origin .sec-title{left:110px;top:136px;color:var(--blue)}
.origin .body-copy{left:110px;width:495px}
.origin-img{left:644px;top:100px;width:556px;height:315px;border-radius:10px 0 0 10px;background:linear-gradient(120deg,#6c5a3f,#c9d34a 40%,#e3e5e8 60%,#8a2a2a)}

/* testimonials */
.reviews{top:2505px;height:587px;background:var(--blue);color:var(--white)}
.reviews .eyebrow{top:46px}
.reviews .sec-title{top:74px}
.quote-card{background:var(--white);border-radius:10px;color:var(--ink);text-align:center;font-size:14.5px;line-height:28px}
.quote-mark{font-family:"Playfair Display",Georgia,serif;font-size:70px;line-height:50px;height:48px}
.avatar{width:92px;height:92px;border-radius:50%;border:3px solid var(--white);background:linear-gradient(160deg,var(--blue-pale),var(--blue-soft))}
.reviewer{font-family:"Raleway",sans-serif;font-weight:700;font-size:20px;text-align:center;width:200px}

/* contact */
.contact{top:3092px;height:616px}
.contact .eyebrow{top:94px;color:var(--ink)}
.contact .sec-title{top:122px;color:var(--blue)}
.field{background:var(--white);border:1px solid #ddd;box-shadow:0 2px 4px rgba(0,0,0,.18);font-size:14.5px;color:#333;padding:12px 10px}

/* footer */
.site-footer{top:3708px;height:301px;background:var(--blue);color:var(--white)}
.foot-brand{left:113px;top:44px;width:190px;height:186px;display:flex;align-items:center;justify-content:center;text-align:center;font-family:"Raleway",sans-serif;font-weight:700;font-size:24px;line-height:1.25}
.foot-col h4{font-family:"Raleway",sans-serif;font-weight:700;font-size:20px;margin-bottom:16px}
.foot-col a{display:block;color:var(--white);text-decoration:none;font-size:15px;line-height:28.5px}
.news-input{left:807px;top:72px;width:284px;height:44px;border-radius:22px;background:var(--white);color:#333;font-size:14px;padding:14px 14px}
.news-btn{left:807px;top:144px;width:118px;background:var(--white);color:var(--ink)}
.copyright{left:0;top:255px;width:1200px;text-align:center;font-size:14.5px}
</style>
</head>
<body>

<header class="site-header">
  <div class="abs topbar"></div>
  <div class="abs topbar-text">Lorem ipsum dolor sit amet, consectetur adipiscing elit, sed do</div>
  <div class="abs social" style="left:996px"></div>
  <div class="abs social" style="left:1031px"></div>
  <div class="abs social" style="left:1064px"></div>

  <div class="abs brand-panel"></div>
  <div class="abs brand">
    <span class="brand-square"></span>
    <span class="brand-name">Keelbrook<br>Maintenance</span>
  </div>

  <div class="abs contact-item" style="left:339px">
    <span class="contact-icon"><svg width="24" height="18" viewBox="0 0 24 18"><rect x="1" y="1" width="22" height="16" rx="2" fill="#fff"/><path d="M2 3l10 7 10-7" stroke="#5a6070" stroke-width="2" fill="none"/></svg></span>
    <span>info@keelbrookmaint.com</span>
  </div>
  <div class="abs contact-item" style="left:626px">
    <span class="contact-icon"><svg width="20" height="26" viewBox="0 0 20 26"><path d="M10 1C5 1 1 5 1 10c0 7 9 15 9 15s9-8 9-15c0-5-4-9-9-9z" fill="#fff"/><circle cx="10" cy="10" r="3.5" fill="#5a6070"/></svg></span>
    <span>Keelbrook Maintenance,Perth<br>Western Australia</span>
  </div>
  <div class="abs contact-item" style="left:888px">
    <span class="contact-icon"><svg width="22" height="22" viewBox="0 0 24 24"><path d="M6.6 10.8a15 15 0 006.6 6.6l2.2-2.2c.3-.3.7-.4 1-.2 1.1.4 2.3.6 3.6.6.6 0 1 .4 1 1V20c0 .6-.4 1-1 1A17 17 0 013 4c0-.6.4-1 1-1h3.5c.6 0 1 .4 1 1 0 1.3.2 2.5.6 3.6.1.3 0 .7-.2 1z" fill="#fff"/></svg></span>
    <span>+1(555)010 0199</span>
  </div>

  <nav>
    <div class="abs navbar"></div>
    <a class="abs nav-link" style="left:343px">Home</a>
    <a class="abs nav-link" style="left:411px">About us</a>
    <a class="abs nav-link" style="left:499px">Services</a>
    <a class="abs nav-link" style="left:584px">Equipment</a>
    <a class="abs nav-link" style="left:685px">Testimonials</a>
    <a class="abs nav-link" style="left:799px">Gallery</a>
    <a class="abs nav-link" style="left:873px">Projects</a>
    <a class="abs nav-link" style="left:956px">Blog</a>
    <a class="abs nav-link" style="left:1014px">Contact us</a>
  </nav>
</header>

<section class="hero" role="img" aria-label="Technician in a hard hat and safety glasses working on machinery">
  <div class="abs hero-welcome">Welcome To</div>
  <div class="abs hero-title">Keelbrook <small>Maintenance</small></div>
  <p class="abs hero-text" style="width:320px">Lorem ipsum dolor sit amet, ipsciulmaecenus vel facilisis.</p>
  <a class="abs btn hero-btn">Get Started</a>
</section>

<section class="about">
  <div class="abs about-name">Keelbrook<br>Maintenance</div>
  <div class="abs eyebrow">Who We Are <span class="rule"></span></div>
  <h2 class="abs sec-title">ABOUT US</h2>
  <p class="abs body-copy">Lorem ipsum dolor sit amet, consectetur adipiscing elit, sed do eiusmod tempor incididunt ut labore et dolore magna aliqua. uis ipsum suspendisse ultrices gravida. Risus commodo viverra nas accumsan lacus vel facilisis. Lorem ipsum dolor sit amet, ectetur adipiscing elit, sed do eiusmod tempor incididunt magnaaliqua. uis ipsum suspendisse ultrices gravida. Risus commodo viverra nas accumsan lacus vel facilisis Lorem ipsum dolor tnsectetur adipiscing elit, sed do eiusmod tempor incididunt ut labore et dolore magna aliqua.</p>
  <a class="abs btn blue-btn" style="left:643px;top:475px">Read More</a>
</section>

<section class="services">
  <div class="abs eyebrow centered" style="display:flex"><span class="rule"></span>What We Do<span class="rule"></span></div>
  <h2 class="abs sec-title centered">SERVICES</h2>

  <div class="abs arrow" style="left:46px;top:271px;background:var(--blue-soft)"><svg width="10" height="14" viewBox="0 0 10 14"><path d="M8 1L2 7l6 6" stroke="#0054AA" stroke-width="2.5" fill="none"/></svg></div>
  <div class="abs arrow" style="left:1119px;top:271px;background:var(--white)"><svg width="10" height="14" viewBox="0 0 10 14"><path d="M2 1l6 6-6 6" stroke="#0054AA" stroke-width="2.5" fill="none"/></svg></div>

  <article class="abs svc-card" style="left:110px">
    <div class="svc-img" role="img" aria-label="Worker inspecting a drill rig" style="background:linear-gradient(135deg,#9aa6ad,#2f6e6a 55%,#c9b13c)"></div>
    <h3 class="svc-name">Drill Rigs</h3>
    <p class="svc-text">Lorem ipsum dolor sit amet, consectetur alabore et dolore magna aliqua.</p>
    <a class="svc-more">Read More</a>
  </article>
  <article class="abs svc-card" style="left:460px">
    <div class="svc-img" role="img" aria-label="Technician servicing a boat propeller" style="background:linear-gradient(135deg,#6a5a70,#2a2a2e 60%,#8a8a8a)"></div>
    <h3 class="svc-name">Large Boats</h3>
    <p class="svc-text">Lorem ipsum dolor sit amet, consectetur alabore et dolore magna aliqua.</p>
    <a class="svc-more">Read More</a>
  </article>
  <article class="abs svc-card" style="left:808px;top:160px">
    <div class="svc-img" role="img" aria-label="Engineer repairing earthmoving machinery" style="background:linear-gradient(135deg,#c0302a,#3a4a6a 55%,#cfd84a)"></div>
    <h3 class="svc-name">Earthmoving Equipment</h3>
    <p class="svc-text">Lorem ipsum dolor sit amet, consectetur alabore et dolore magna aliqua.</p>
    <a class="svc-more">Read More</a>
  </article>
</section>

<section class="origin">
  <div class="abs eyebrow">Where We Come From <span class="rule"></span></div>
  <h2 class="abs sec-title">WHERE WE COME FROM</h2>
  <p class="abs body-copy" style="top:196px">Director of the company has over 20-year experience in the fixed and ile plant industries ranging from Perth local and overseas. Facilities fining, offshore drilling and production platform, open cut and undergrounding, civils, geotechnical and construction equipment and large-scale ruction as an expat overseas.</p>
  <p class="abs body-copy" style="top:346px">We offer personalised service to all small and medium size business across a diverse range of industries.</p>
  <div class="abs origin-img" role="img" aria-label="Two engineers in hard hats and hi-vis vests working on equipment"></div>
</section>

<section class="reviews">
  <div class="abs eyebrow centered" style="display:flex"><span class="rule"></span>Our Reviews<span class="rule"></span></div>
  <h2 class="abs sec-title centered">TESTIMONIALS</h2>

  <div class="abs arrow" style="left:56px;top:301px;background:var(--blue-soft)"><svg width="10" height="14" viewBox="0 0 10 14"><path d="M8 1L2 7l6 6" stroke="#0054AA" stroke-width="2.5" fill="none"/></svg></div>
  <div class="abs arrow" style="left:1129px;top:301px;background:var(--white)"><svg width="10" height="14" viewBox="0 0 10 14"><path d="M2 1l6 6-6 6" stroke="#0054AA" stroke-width="2.5" fill="none"/></svg></div>

  <div class="abs quote-card" style="left:113px;top:222px;width:327px;height:223px;padding:10px 20px">
    <div class="quote-mark" style="color:#bbb">&ldquo;</div>
    <p>Lorem ipsum dolor sit amet, consectetur adipiscing elit, sed do eiusmod tempor indunt ut labore et dolore magna aliqua. lacus vel facilisis.</p>
  </div>
  <div class="abs quote-card" style="left:761px;top:222px;width:327px;height:223px;padding:10px 20px">
    <div class="quote-mark" style="color:#bbb">&ldquo;</div>
    <p>Lorem ipsum dolor sit amet, consectetur adipiscing elit, sed do eiusmod tempor incidunt ut labore et dolore magna aliqua. lacus vel facilisis.</p>
  </div>
  <div class="abs quote-card" style="left:428px;top:172px;width:344px;height:222px;padding:10px 24px;box-shadow:0 4px 14px rgba(0,0,0,.25)">
    <div class="quote-mark" style="color:#222">&ldquo;</div>
    <p>Lorem ipsum dolor sit amet, consectetur adipiscing elit, sed do eiusmod tempor indunt ut labore et dolore magna aliqua. lacus vel facilisis.</p>
  </div>

  <div class="abs avatar" role="img" aria-label="Client portrait" style="left:229px;top:407px"></div>
  <div class="abs avatar" role="img" aria-label="Client portrait" style="left:553px;top:355px"></div>
  <div class="abs avatar" role="img" aria-label="Client portrait" style="left:878px;top:407px"></div>
  <div class="abs reviewer" style="left:175px;top:507px">Graham Doyle</div>
  <div class="abs reviewer" style="left:498px;top:455px">Owen Pritchard</div>
  <div class="abs reviewer" style="left:822px;top:507px">Lewis Carden</div>
</section>

<section class="contact">
  <div class="abs eyebrow centered" style="display:flex"><span class="rule" style="background:#111"></span>Get In Touch<span class="rule" style="background:#111"></span></div>
  <h2 class="abs sec-title centered">CONTACT US</h2>
  <div class="abs field" style="left:259px;top:210px;width:328px;height:42px">Your Name</div>
  <div class="abs field" style="left:610px;top:210px;width:328px;height:42px">Phone Number</div>
  <div class="abs field" style="left:259px;top:272px;width:328px;height:42px">Email Address</div>
  <div class="abs field" style="left:610px;top:272px;width:328px;height:42px">Subject</div>
  <div class="abs field" style="left:259px;top:331px;width:679px;height:125px">Your Message</div>
  <a class="abs btn blue-btn" style="left:544px;top:485px">Submit</a>
</section>

<footer class="site-footer">
  <div class="abs foot-brand">Keelbrook<br>Maintenance</div>
  <div class="abs foot-col" style="left:413px;top:48px">
    <h4>Quick Links</h4>
    <a>Home</a><a>About us</a><a>Services</a><a>Equipment</a><a>Testimonials</a>
  </div>
  <div class="abs foot-col" style="left:601px;top:48px">
    <h4>Other Links</h4>
    <a>Gallery</a><a>Projects</a><a>Blog</a><a>Contact us</a>
  </div>
  <div class="abs foot-col" style="left:807px;top:46px"><h4>Subscribe To Our Newsletter</h4></div>
  <div class="abs news-input">Email Address</div>
  <a class="abs btn news-btn">Subscribe</a>
  <div class="abs copyright">&copy; 2024 Keelbrook Maintenance | all Rights Reserved</div>
</footer>

</body>
</html>
```